New florist business website design

Number 1 want is an easy to navigate & check out website
Needs to be beautiful and eye catching as well.
This is an online only business (no shop front)
Rustic and blush pinks, neutrals, woods, leaves
Customers need to be able to go onto my website, select something they want to buy but have the option to use a drop down box to change colours of the flowers, or add notes to make changes to the arrangement

Industry/Entity Type

Florist

Coding

Coded - Design and coding required

Number of Pages Required

5+ page

Colors
f9d9e8
fff2ec
fffefc

Requirements
Must have
• Drop down menu to take you to other pages for Arrangements, bouquets, everlasting arrangements, gifts, contact
Be able to purchase and “add to basket”
Checkout page
Nice to have
• Be able to add my own photos once I’ve taken new ones
Should not have
• Tacky images or clip art

```html
<!DOCTYPE html>
<html lang="en">
<head>
<meta charset="utf-8">
<title>Bloom &amp; Fern — Florist</title>
<link href="https://fonts.googleapis.com/css2?family=Quicksand:wght@400;500;600&family=Caveat:wght@400&display=swap" rel="stylesheet">
<style>
:root{
  --blush:#f9d9e8;
  --blush-deep:#f5cde0;
  --header:#fbe7ec;
  --peach:#fff2ec;
  --peach-panel:#fbe6d6;
  --cream:#fffefc;
  --mauve:#e5c2d5;
  --footer:#fceaec;
  --ink:#1e1e1e;
  --text:#333;
  --muted:#777;
  --star:#f5a623;
  --magenta:#e020c8;
}
*{margin:0;padding:0;box-sizing:border-box}
html,body{width:1200px;height:3849px;overflow:hidden}
body{position:relative;background:var(--cream);font-family:'Quicksand',sans-serif;color:var(--text)}
.abs{position:absolute}
.script{font-family:'Caveat',cursive}
.center{left:0;width:1200px;text-align:center}

.site-header{top:0;left:0;width:1200px;height:78px;background:var(--header);z-index:3}
.logo-box{top:0;left:88px;width:167px;height:139px;background:var(--header);z-index:4;display:flex;align-items:center;justify-content:center}
.brand{font-family:'Quicksand',sans-serif;font-weight:500;color:var(--ink);font-size:22px;white-space:nowrap}
.main-nav{top:30px;left:0;width:1200px;z-index:4;font-size:14px;font-weight:500;color:var(--ink)}
.main-nav span{position:absolute;white-space:nowrap}
.header-icons{top:30px;z-index:4}

.hero{top:78px;left:0;width:1200px;height:597px;background:linear-gradient(120deg,#e9ebee 0%,#f3f3f5 45%,#e6e7ea 100%)}
.hero-leaf-l{top:78px;left:0;width:260px;height:597px;background:linear-gradient(90deg,rgba(60,90,50,.55),rgba(60,90,50,0))}
.hero-bloom-r{top:78px;left:900px;width:300px;height:597px;background:linear-gradient(270deg,rgba(240,215,195,.9),rgba(240,215,195,0))}
.hero-kicker{top:262px;font-size:34px;color:var(--ink)}
.hero-title{top:308px;font-size:44px;line-height:52px;font-weight:400;color:var(--ink)}
.hero-btn{top:432px;left:517px;width:164px;height:51px;border:2px solid var(--ink);display:flex;align-items:center;justify-content:center;font-size:26px;color:var(--ink)}
.side-label{font-size:12px;font-weight:600;letter-spacing:0;line-height:22px;width:12px;text-align:center;color:var(--ink)}

.vline{width:1px;background:#888}
.arrow-head{width:0;height:0;border-left:6px solid transparent;border-right:6px solid transparent;border-top:9px solid #888}
.scroll-text{top:730px;font-size:16px;color:var(--muted)}
.vertical{writing-mode:vertical-rl;font-size:15px;color:var(--ink)}

.welcome{top:774px;left:221px;width:758px;height:421px;background:var(--blush-deep);text-align:center}
.welcome .eyebrow{margin-top:32px;font-size:13px;color:var(--ink)}
.welcome h2{margin-top:10px;font-size:35px;line-height:43px;font-weight:400;color:var(--ink)}
.welcome p{margin:20px auto 0;width:520px;font-size:15px;line-height:30px;color:var(--text)}
.welcome .script{display:block;margin-top:10px;font-size:20px;color:var(--ink)}
.learn{font-size:13px;color:var(--ink);letter-spacing:.3px}

.photo{position:absolute}
.everlasting h2{position:absolute;top:1510px;left:662px;font-size:29px;font-weight:400;color:var(--ink)}
.everlasting p{position:absolute;top:1560px;left:662px;width:464px;font-size:15px;line-height:30px;color:var(--text)}

.trending{top:2060px;left:0;width:1200px;height:746px;background:var(--mauve)}
.trending h2{position:absolute;top:2134px;font-size:35px;font-weight:400;color:var(--ink)}
.card{position:absolute;top:2226px;width:317px;height:469px;background:#fff;box-shadow:0 2px 8px rgba(0,0,0,.08);text-align:center}
.card .thumb{position:absolute;top:37px;left:78px;width:161px;height:195px;border-radius:40% 40% 30% 30%}
.card .name{position:absolute;top:264px;left:0;width:100%;font-size:17px;color:var(--ink)}
.card .price{position:absolute;top:294px;left:0;width:100%;font-size:17px;font-weight:600;color:var(--ink)}
.card .price s{font-size:11px;color:var(--muted);font-weight:500;margin-left:4px}
.card .stars{position:absolute;top:322px;left:0;width:100%;color:var(--star);font-size:14px;letter-spacing:1px}
.card .swatches{position:absolute;top:350px;left:0;width:100%;display:flex;justify-content:center;gap:2px}
.card .swatches i{width:11px;height:11px;border-radius:50%;display:block}
.card .cart{position:absolute;top:382px;left:67px;width:184px;height:50px;border:2px solid var(--ink);display:flex;align-items:center;justify-content:center;font-size:17px;color:var(--ink)}

.reviews h2{position:absolute;top:2884px;font-size:35px;font-weight:400;color:var(--ink)}
.reviews p{position:absolute;top:2960px;left:191px;width:820px;text-align:center;font-style:italic;font-size:13.5px;line-height:30px;color:var(--text)}
.reviews .author{position:absolute;top:3094px;font-size:17px;color:var(--ink)}
.dot{position:absolute;left:1062px;width:10px;height:10px;border-radius:50%}

.site-footer{top:3190px;left:0;width:1200px;height:659px;background:var(--footer)}
.subscribe-title{top:3288px;left:82px;font-size:33px;font-weight:500;color:var(--ink)}
.email-input{top:3279px;left:448px;width:459px;height:48px;border:1px solid #999;background:#fff;font-size:12px;color:var(--muted);padding:0 15px;display:flex;align-items:center}
.subscribe-btn{top:3279px;left:919px;width:167px;height:48px;background:var(--blush-deep);display:flex;align-items:center;justify-content:center;font-size:17px;color:var(--ink)}
.footer-brand{top:3420px;font-size:30px}
.contact-line{font-size:14px;color:var(--ink);display:flex;justify-content:center;align-items:center;gap:10px}
.social{position:absolute;top:3648px;width:54px;height:54px;border-radius:50%;background:#111}
.footer-nav{top:3731px}
.copyright{top:3785px;left:148px;font-size:13px;color:var(--text)}
.pay{position:absolute;top:3790px;width:24px;height:15px;border-radius:2px}
</style>
</head>
<body>

<header>
  <div class="abs site-header"></div>
  <div class="abs logo-box"><span class="brand">Bloom &amp; Fern</span></div>
  <nav class="abs main-nav">
    <span style="left:317px">Home</span>
    <span style="left:386px">Arrangements</span>
    <span style="left:514px">Bouquets</span>
    <span style="left:608px">Everlasting Arrangements</span>
    <span style="left:816px">Gifts</span>
    <span style="left:877px">Contact Us</span>
  </nav>
  <svg class="abs header-icons" style="left:1009px" width="90" height="16" viewBox="0 0 90 16" aria-hidden="true">
    <path d="M1 5h12l-1 10H2z M4 5V3a3 3 0 0 1 6 0v2" fill="#111" stroke="#111" stroke-width="1.2"/>
    <circle cx="43" cy="5" r="3.5" fill="#111"/><path d="M37 15c0-4 3-6 6-6s6 2 6 6z" fill="#111"/>
    <path d="M77 14l-6-6a3.5 3.5 0 0 1 6-4a3.5 3.5 0 0 1 6 4z" fill="#111"/>
  </svg>
</header>

<section class="hero-section">
  <div class="abs hero" role="img" aria-label="Flat-lay photo of peonies, green leaves and clear crystals on a soft grey surface"></div>
  <div class="abs hero-leaf-l" aria-hidden="true"></div>
  <div class="abs hero-bloom-r" aria-hidden="true"></div>
  <div class="abs center script hero-kicker">Lorem ipsum dolor sit amet</div>
  <h1 class="abs center hero-title">Lorem ipsum dolor sit amet, consectetur<br>adipiscing elit, sed do eiusmod</h1>
  <div class="abs hero-btn script">GET STARTED</div>
  <div class="abs side-label" style="top:316px;left:44px">P<br>R<br>E<br>V</div>
  <div class="abs side-label" style="top:316px;left:1145px">N<br>E<br>X<br>T</div>
  <div class="abs vline" style="top:575px;left:600px;height:135px"></div>
  <div class="abs arrow-head" style="top:710px;left:594px"></div>
  <div class="abs center script scroll-text">SCROLL DOWN</div>
</section>

<section class="intro">
  <div class="abs welcome">
    <div class="eyebrow">WELCOME TO BLOOM &amp; FERN</div>
    <h2>WE PRODUCE BEAUTY INSPIRED<br>BY FLORA</h2>
    <p>Lorem ipsum dolor sit amet, consectetur adipiscing elit, sed do eiusmod tempor incididunt ut labore et dolore magna aliqua. Quis ipsum suspendisse ultrices gravida. Risus commodo viverra maecenas accumsan lacus vel facilisis.</p>
    <span class="script">Lorem ipsum dolor sit amet</span>
    <div class="learn">LEARN MORE</div>
  </div>
  <div class="photo" style="top:1034px;left:722px;width:478px;height:394px;background:radial-gradient(circle at 50% 45%,#f2a77e 0%,#f3d2bf 35%,#b8c9a2 65%,#8f98a3 100%)" role="img" aria-label="Photo of a peach and cream rose arrangement in a rustic box"></div>
  <div class="abs vline" style="top:1153px;left:677px;height:140px"></div>
  <div class="abs arrow-head" style="top:1292px;left:671px"></div>
  <div class="abs vertical" style="top:1322px;left:668px">Arrangements</div>
</section>

<section class="everlasting">
  <div class="photo" style="top:1428px;left:0;width:599px;height:553px;background:linear-gradient(135deg,#f5d5c4,#fbe6d6 60%,#fcebdf)" role="img" aria-label="Soft faded photo of pale roses"></div>
  <div class="photo" style="top:1539px;left:206px;width:372px;height:499px;background:radial-gradient(circle at 50% 50%,#f3f0ea 0%,#e8a07f 30%,#5d8a3e 60%,#2c3328 100%)" role="img" aria-label="Photo of a mixed bouquet with lilies, white chrysanthemums and green blooms"></div>
  <h2>EVERLASTING ARRANGEMENTS</h2>
  <p>Lorem ipsum dolor sit amet, consectetur adipiscing elit, sed do eiusmod tempor incididunt ut labore et dolore magna aliqua. Ut enim ad minim veniam, quis nostrud exercitation ullamco laboris nisi ut aliquip ex ea commodo consequat. Duis aute irure dolor in reprehenderit in voluptate velit esse cillum dolore eu fugiat nulla pariatur. Excepteur sint occaecat cupidatat non proident, sunt in culpa qui officia deserunt mollit anim id est laborum.</p>
  <div class="abs script" style="top:1772px;left:662px;font-size:18px;color:var(--ink)">Lorem ipsum dolor sit amet</div>
  <div class="abs learn" style="top:1810px;left:662px">LEARN MORE</div>
  <div class="abs vline" style="top:1850px;left:668px;height:48px"></div>
  <div class="abs arrow-head" style="top:1898px;left:662px"></div>
  <div class="abs vertical" style="top:1925px;left:660px">Scroll</div>
  <div class="photo" style="top:1830px;left:896px;width:304px;height:230px;background:radial-gradient(ellipse at 70% 70%,#e98a8a 0%,#f4c2bb 45%,rgba(255,254,252,0) 75%)" role="img" aria-label="Photo of pink tulips"></div>
</section>

<section class="trending-section">
  <div class="abs trending" role="img" aria-label="Faded background photo of pink blossoms"></div>
  <h2 class="center">Our Trending Products</h2>

  <div class="card" style="left:109px">
    <div class="thumb" style="background:radial-gradient(circle,#e84a6a,#c22a3a 45%,#3e6b2d 75%,#fff 76%)" role="img" aria-label="Photo of a red and pink mixed bouquet"></div>
    <div class="name">Product Name</div>
    <div class="price">$129.00<s>$200.00</s></div>
    <div class="stars">★★★★★</div>
    <div class="swatches"><i style="background:var(--magenta)"></i><i style="background:#e79ee0"></i><i style="background:#c2a0bb"></i></div>
    <div class="cart">Add to Cart</div>
  </div>
  <div class="card" style="left:441px">
    <div class="thumb" style="background:radial-gradient(circle,#f7d13b,#e8467a 45%,#3e6b2d 75%,#fff 76%)" role="img" aria-label="Photo of a bright pink and yellow gerbera bouquet"></div>
    <div class="name">Product Name</div>
    <div class="price">$129.00<s>$200.00</s></div>
    <div class="stars">★★★★★</div>
    <div class="swatches"><i style="background:var(--magenta)"></i><i style="background:#e79ee0"></i><i style="background:#c2a0bb"></i></div>
    <div class="cart">Add to Cart</div>
  </div>
  <div class="card" style="left:771px">
    <div class="thumb" style="background:linear-gradient(180deg,#b5127a 0%,#d0207e 45%,#5d8f3a 60%,#4a7a2f 100%);border-radius:45% 45% 10% 10%" role="img" aria-label="Photo of a magenta tulip bouquet"></div>
    <div class="name">Product Name</div>
    <div class="price">$129.00<s>$200.00</s></div>
    <div class="stars">★★★★★</div>
    <div class="swatches"><i style="background:var(--magenta)"></i><i style="background:#e79ee0"></i><i style="background:#c2a0bb"></i></div>
    <div class="cart">Add to Cart</div>
  </div>
</section>

<section class="reviews">
  <h2 class="center">OUR CUSTOMERS REVIEWS</h2>
  <p>Lorem ipsum dolor sit amet, consectetur adipiscing elit, sed do eiusmod tempor incididunt ut labore et dolore magna aliqua. Quis ipsum suspendisse ultrices gravida. Risus commodo viverra maecenas accumsan lacus vel facilisis.Ut enim ad minim veniam, quis nostrud exercitation ullamco laboris nisi ut aliquip ex ea commodo consequat. Duis aute irure dolor in reprehenderit in voluptate velit.</p>
  <div class="author center">Marlowe</div>
  <span class="dot" style="top:2975px;background:#111"></span>
  <span class="dot" style="top:3002px;background:var(--blush-deep)"></span>
  <span class="dot" style="top:3029px;background:#111"></span>
</section>

<footer>
  <div class="abs site-footer"></div>
  <div class="abs subscribe-title">Subscribe Newsletter</div>
  <div class="abs email-input">Enter The Email</div>
  <div class="abs subscribe-btn">Subscribe</div>

  <div class="abs center brand footer-brand">Bloom &amp; Fern</div>

  <div class="abs center contact-line" style="top:3512px">
    <svg width="10" height="14" viewBox="0 0 10 14" aria-hidden="true"><path d="M5 0a5 5 0 0 1 5 5c0 4-5 9-5 9S0 9 0 5a5 5 0 0 1 5-5z" fill="#111"/><circle cx="5" cy="5" r="2" fill="#fceaec"/></svg>
    123 Lorem ipsum dolor sit amet, consectetur adipiscing elit
  </div>
  <div class="abs center contact-line" style="top:3554px">
    <svg width="13" height="13" viewBox="0 0 13 13" aria-hidden="true"><path d="M3 0l2 3-1.5 1.5a8 8 0 0 0 5 5L10 8l3 2-1.5 3C6 13 0 7 0 1.5z" fill="#111"/></svg>
    555 014 2290
  </div>
  <div class="abs center contact-line" style="top:3597px">
    <svg width="14" height="11" viewBox="0 0 14 11" aria-hidden="true"><rect width="14" height="11" fill="#111"/><path d="M0 0l7 6 7-6" fill="none" stroke="#fceaec" stroke-width="1.3"/></svg>
    hello@bloomandfern.com
  </div>

  <span class="social" style="left:421px"></span>
  <span class="social" style="left:496px"></span>
  <span class="social" style="left:571px;background:var(--blush-deep)"></span>
  <span class="social" style="left:647px"></span>
  <span class="social" style="left:723px"></span>

  <nav class="abs main-nav footer-nav">
    <span style="left:317px">Home</span>
    <span style="left:386px">Arrangements</span>
    <span style="left:514px">Bouquets</span>
    <span style="left:608px">Everlasting Arrangements</span>
    <span style="left:816px">Gifts</span>
    <span style="left:877px">Contact Us</span>
  </nav>

  <div class="abs copyright">© Copyrights 2021 Bloom &amp; Fern &nbsp;|&nbsp; All Rights Reserved</div>
  <span class="pay" style="left:919px;background:#333"></span>
  <span class="pay" style="left:947px;background:#d9dde3"></span>
  <span class="pay" style="left:975px;background:#d9dde3"></span>
  <span class="pay" style="left:1003px;background:#d9dde3"></span>
  <span class="pay" style="left:1031px;background:#3a6fb5"></span>
  <span class="pay" style="left:1059px;background:#d8452e"></span>
</footer>

</body>
</html>
```